Bourbon label design for bourbon brand. Looking to freshen our current label.

I need a Bourbon label design for our rebranded Bourbon bottle. Label should include picture of our horse and our logo on the bottle. Front Label is 3.5 inches wide and 6 inches tall, back label is 4 inches tall and 3 inches wide. Back label can be a simple plain logo like the one in the brief. I have included a design of our current bottle and label. We want to stay close to the current color schemes but want a fresh rebrand of the design. The label needs to be the correct size on a tall bottle like pictured.

Target Market(s)

Our Bourbon members, 30-50 year old males

Requirements
Must have
• Picture of our horse, our B logo , straight Bourbon whiskey on the front. Room to edit text on the back label.

```html
<!DOCTYPE html>
<html lang="en">
<head>
<meta charset="utf-8">
<title>Nightfall Straight Bourbon Whiskey – Label Set</title>
<link rel="stylesheet" href="https://fonts.googleapis.com/css2?family=Fjalla+One&family=Montserrat:wght@400&display=swap">
<style>
  :root {
    --board: #dcdcdc;
    --ink: #0d0d0d;
    --steel: #5e5e5e;
    --steel-dark: #555555;
    --silver-top: #9e9e9e;
    --silver-bottom: #ffffff;
    --white: #ffffff;
    --photo-dark: #6f6f6f;
    --photo-light: #c9c9c9;
  }
  * { box-sizing: border-box; margin: 0; padding: 0; }
  html, body { width: 1000px; height: 1200px; overflow: hidden; }
  body { background: var(--board); position: relative; font-family: "Fjalla One", sans-serif; }

  .label { position: absolute; overflow: hidden; }
  .label-bg { position: absolute; inset: 0; width: 100%; height: 100%; }

  /* Front label */
  .front-label { left: 70px; top: 224px; width: 440px; height: 754px; }
  .brand-title { position: absolute; left: 36px; top: 86px; line-height: 65px; font-size: 74px; text-transform: uppercase; letter-spacing: -0.5px; }
  .brand-title .brand-name { color: var(--ink); display: block; }
  .brand-title .style-line { color: var(--steel); display: block; }

  .est-mark { position: absolute; color: var(--white); font-size: 18px; letter-spacing: 1px; text-align: center;
              border-top: 1.5px solid var(--white); border-bottom: 1.5px solid var(--white); padding: 5px 0 6px; }
  .front-label .est-mark { left: 359px; top: 75px; width: 64px; }

  .feature { position: absolute; left: 38px; color: var(--ink); font-size: 19px; line-height: 23px; text-transform: uppercase; }
  .feature::after { content: ""; display: block; width: 30px; height: 3px; background: var(--steel); margin-top: 8px; }
  .feature-single { top: 375px; }
  .feature-strength { top: 458px; }

  .horse-photo { position: absolute; left: 205px; top: 364px; width: 161px; height: 323px; }

  .logo-name { position: absolute; font-size: 13px; letter-spacing: 1px; text-transform: uppercase; display: flex; align-items: center; gap: 5px; }
  .logo-name .dot { width: 7px; height: 7px; border-radius: 50%; background: currentColor; }
  .front-label .logo-name { left: 352px; top: 662px; color: var(--white); }

  .fill-fields { position: absolute; left: 40px; top: 688px; display: flex; gap: 13px; }
  .fill-field { width: 80px; font-size: 12px; color: var(--ink); text-transform: uppercase; border-bottom: 1.5px solid var(--steel); padding-bottom: 4px; }

  /* Back label */
  .back-label { left: 590px; top: 224px; width: 340px; height: 450px; }
  .back-copy { position: absolute; left: 29px; top: 53px; width: 210px; font-family: "Montserrat", sans-serif; font-size: 12.2px; line-height: 15.8px; color: var(--ink); }
  .back-copy p + p { margin-top: 15px; }
  .back-title { position: absolute; left: 265px; top: 55px; font-size: 16px; line-height: 14.5px; text-transform: uppercase; }
  .back-title .brand-name { color: var(--white); display: block; }
  .back-title .style-line { color: #8a8a8a; display: block; }
  .back-label .est-mark { left: 279px; top: 376px; width: 42px; font-size: 12px; padding: 3px 0 4px; border-width: 1px; }
  .back-label .logo-name { left: 29px; top: 382px; color: var(--ink); }
</style>
</head>
<body>

<section class="label front-label" aria-label="Front label">
  <svg class="label-bg" viewBox="0 0 576 987" preserveAspectRatio="none" aria-hidden="true">
    <defs>
      <linearGradient id="front-silver" x1="0" y1="0" x2="0" y2="1">
        <stop offset="0" stop-color="#9e9e9e"/>
        <stop offset="0.55" stop-color="#cfcfcf"/>
        <stop offset="0.85" stop-color="#ffffff"/>
      </linearGradient>
    </defs>
    <rect width="576" height="987" fill="url(#front-silver)"/>
    <path d="M344,0 H576 V954 H504 A60,60 0 0 1 444,894 V100 A100,100 0 0 0 344,0 Z" fill="#0d0d0d"/>
  </svg>

  <h1 class="brand-title">
    <span class="brand-name">Nightfall</span>
    <span class="style-line">Straight</span>
    <span class="style-line">Bourbon</span>
    <span class="style-line">Whiskey</span>
  </h1>

  <div class="est-mark">EST. 2016</div>

  <div class="feature feature-single">Single<br>Barrel</div>
  <div class="feature feature-strength">Barrel<br>Strength</div>

  <svg class="horse-photo" role="img" aria-label="Black and white photo of the brand's racehorse with jockey galloping toward the viewer" viewBox="0 0 161 323" preserveAspectRatio="none">
    <defs>
      <radialGradient id="horse-tone" cx="0.5" cy="0.45" r="0.6">
        <stop offset="0" stop-color="#7a7a7a"/>
        <stop offset="0.7" stop-color="#a8a8a8"/>
        <stop offset="1" stop-color="#d6d6d6" stop-opacity="0"/>
      </radialGradient>
    </defs>
    <ellipse cx="80" cy="160" rx="80" ry="162" fill="url(#horse-tone)"/>
  </svg>

  <div class="logo-name"><span class="dot"></span>Nightfall</div>

  <div class="fill-fields">
    <div class="fill-field">Barrel No.</div>
    <div class="fill-field">Aged/Years</div>
    <div class="fill-field">Alc./Vol.</div>
  </div>
</section>

<section class="label back-label" aria-label="Back label">
  <svg class="label-bg" viewBox="0 0 499 660" preserveAspectRatio="none" aria-hidden="true">
    <defs>
      <linearGradient id="back-silver" x1="0" y1="0" x2="0" y2="1">
        <stop offset="0" stop-color="#9e9e9e"/>
        <stop offset="0.6" stop-color="#d4d4d4"/>
        <stop offset="0.95" stop-color="#ffffff"/>
      </linearGradient>
    </defs>
    <rect width="499" height="660" fill="url(#back-silver)"/>
    <path d="M273,0 H499 V628 H433 A60,60 0 0 1 373,568 V100 A100,100 0 0 0 273,0 Z" fill="#0d0d0d"/>
  </svg>

  <div class="back-copy">
    <p>Lorem ipsum dolor sit amet, consectetur adipiscing elit. Quisque placerat sem at nunc venenatis venenatis. Vestibulum dapibus dui lectus, non accumsan mauris tincidunt et. In non viverra turpis.</p>
    <p>Aenean id finibus magna, et feugiat ipsum. Proin laoreet gravida lorem nec porta. Suspendisse a neque dictum, tempus lorem ac, suscipit dolor. Fusce id eleifend dolor. Quisque rhoncus sem vel tortor dapibus accumsan.</p>
  </div>

  <div class="back-title">
    <span class="brand-name">Nightfall</span>
    <span class="style-line">Straight</span>
    <span class="style-line">Bourbon</span>
    <span class="style-line">Whiskey</span>
  </div>

  <div class="logo-name"><span class="dot"></span>Nightfall</div>
  <div class="est-mark">EST. 2016</div>
</section>

</body>
</html>
```